BRIGHT RIVER POWER.

I'd like my business logo.
contact name: Dennis Halvorsen
phone:0438759164
email: info@brightriverpower.net.au
website: www.brightriverpower.net.au

services:
solar
battery storage
LED lighting
energy saving solutions
general electrical
I'd like the design to look professional

Target Market(s)

Everyone

Industry/Entity Type

Business

Contact Information for Business Card

as described above

Requirements
Must have
• Id like the colours and the design to work well with my logo.

```html
<!DOCTYPE html>
<html lang="en">
<head>
<meta charset="utf-8">
<title>Bright River Power — Business Card</title>
<link href="https://fonts.googleapis.com/css2?family=Open+Sans:wght@400;600;700&display=swap" rel="stylesheet">
<style>
  :root {
    --stage: #ecebe8;
    --card-top: #f7f6f4;
    --brand-green: #6cbf2f;
    --brand-orange: #f4a21c;
    --green-top: #9ccc2f;
    --green-bottom: #57b874;
    --orange-top: #ffc20e;
    --orange-bottom: #f7941d;
    --ink-light: #ffffff;
  }
  * { box-sizing: border-box; margin: 0; padding: 0; }
  html, body { width: 1200px; height: 900px; overflow: hidden; }
  body {
    position: relative;
    background: var(--stage);
    font-family: "Open Sans", Arial, sans-serif;
  }
  .card {
    position: absolute;
    display: flex;
    flex-direction: column;
    box-shadow: 0 8px 24px rgba(0,0,0,0.12);
    overflow: hidden;
  }
  .card-front { left: 238px; top: 62px; width: 555px; height: 343px; }
  .card-back  { left: 459px; top: 518px; width: 560px; height: 344px; }

  .card-head {
    background: var(--card-top);
    display: flex;
    align-items: center;
    justify-content: center;
    gap: 14px;
  }
  .card-front .card-head { height: 186px; padding-bottom: 6px; }
  .card-back .card-head { height: 187px; }

  .brand-dot {
    width: 46px; height: 46px;
    border-radius: 50%;
    background: var(--brand-orange);
    flex: none;
  }
  .brand-name {
    font-weight: 700;
    font-size: 34px;
    letter-spacing: 1px;
    color: var(--brand-green);
    line-height: 1;
  }
  .brand-ghost { opacity: 0.22; }

  .band-green {
    flex: 1;
    background: linear-gradient(180deg, var(--green-top), var(--green-bottom));
    display: flex;
    align-items: center;
    color: var(--ink-light);
  }
  .holder-name {
    width: 254px;
    text-align: center;
    font-weight: 700;
    font-size: 18px;
    padding-left: 30px;
  }
  .contact-list { list-style: none; font-size: 14px; line-height: 20px; padding-left: 0; }
  .contact-list li { display: flex; align-items: center; gap: 8px; }
  .contact-list svg { width: 11px; height: 11px; fill: var(--ink-light); flex: none; }

  .band-orange {
    flex: 1;
    background: linear-gradient(180deg, var(--orange-top), var(--orange-bottom));
    color: var(--ink-light);
    text-align: center;
    padding-top: 38px;
  }
  .services-title { font-weight: 700; font-size: 16px; margin-bottom: 17px; }
  .services-list { font-size: 14.5px; line-height: 20px; }
</style>
</head>
<body>

  <section class="card card-front" aria-label="Business card front">
    <header class="card-head">
      <span class="brand-dot"></span>
      <span class="brand-name">BRIGHT RIVER POWER</span>
    </header>
    <div class="band-green">
      <p class="holder-name">Dennis Halvorsen</p>
      <ul class="contact-list">
        <li>
          <svg viewBox="0 0 24 24"><path d="M6.6 10.8a15.1 15.1 0 0 0 6.6 6.6l2.2-2.2a1 1 0 0 1 1-.25 11.4 11.4 0 0 0 3.6.57 1 1 0 0 1 1 1V20a1 1 0 0 1-1 1A17 17 0 0 1 3 4a1 1 0 0 1 1-1h3.5a1 1 0 0 1 1 1c0 1.25.2 2.45.57 3.57a1 1 0 0 1-.25 1z"/></svg>
          0438759164
        </li>
        <li>
          <svg viewBox="0 0 24 24"><path d="M2 5h20v14H2z M2 5l10 8 10-8" /></svg>
          info@brightriverpower.net.au
        </li>
        <li>
          <svg viewBox="0 0 24 24"><circle cx="12" cy="12" r="10"/></svg>
          www.brightriverpower.net.au
        </li>
      </ul>
    </div>
  </section>

  <section class="card card-back" aria-label="Business card back">
    <header class="card-head brand-ghost">
      <span class="brand-dot"></span>
      <span class="brand-name">BRIGHT RIVER POWER</span>
    </header>
    <div class="band-orange">
      <h2 class="services-title">WHAT I DO</h2>
      <p class="services-list">Solar | Battery Storage<br>LED Lighting | Energy Saving Solutions</p>
    </div>
  </section>

</body>
</html>
```